Finiding oppertunites in Real Estate 6.15.20

size of ad 7” x 9.6”
1-I like the ad to stand out and attract people's attention.
2-you should be able to see the text of the ad clearly .. see the attachment anything in yellow is instructions.
3-the list of topics should not be the main part of the ad
4-if you decide you want a picture or vector of a person .. (you decide)
then it should be a white male about 25-30 years old wearing a solid white or blue shirt and not long hair.
5-leave 1 inch for footer
see attachment
Good luck

Target Market(s)

potential male students 25-35 years of age

Industry/Entity Type

Education

Requirements
Must have
• will stand out and people would want to see it.
should be able to read the words of ad
Nice to have
• how to make money in real estate on one line

```html
<!DOCTYPE html>
<html lang="en">
<head>
<meta charset="utf-8">
<title>Real Estate Course – 12th Session</title>
<link href="https://fonts.googleapis.com/css2?family=Montserrat:wght@600;700;800;900&family=Poppins:wght@400;500;600&display=swap" rel="stylesheet">
<style>
  :root {
    --blue: #1d6fd6;
    --blue-bright: #2b86ea;
    --navy: #0f2346;
    --sky: #dcecfb;
    --sky-soft: #eef5fd;
    --white: #ffffff;
    --ink: #1b2a44;
  }
  * { box-sizing: border-box; margin: 0; padding: 0; }
  html, body { width: 876px; height: 1200px; overflow: hidden; background: var(--white); }
  .flyer {
    position: relative;
    width: 876px;
    height: 1200px;
    overflow: hidden;
    background: linear-gradient(180deg, #ffffff 0%, #f7fafe 60%, #ffffff 100%);
    font-family: "Poppins", Arial, sans-serif;
    color: var(--ink);
  }
  .corner-wave { position: absolute; top: 0; right: 0; width: 360px; height: 230px; }

  .course-title {
    position: absolute; top: 94px; left: 0; width: 100%;
    text-align: center;
    font-family: "Montserrat", Arial, sans-serif;
    font-weight: 900; font-size: 60px; letter-spacing: 1px; line-height: 1.1;
    color: var(--blue);
  }
  .headline {
    position: absolute; top: 174px; left: 0; width: 100%;
    text-align: center;
    font-family: "Montserrat", Arial, sans-serif;
    font-weight: 800; font-size: 37px; line-height: 1.2;
    color: var(--navy);
  }
  .headline .accent { color: var(--blue); }

  .tagline {
    position: absolute; top: 230px; left: 98px; width: 680px; height: 42px;
    background: var(--blue);
    border-radius: 21px;
    color: var(--white);
    font-family: "Montserrat", Arial, sans-serif;
    font-weight: 600; font-size: 20px; line-height: 42px;
    text-align: center;
    white-space: nowrap;
  }
  .tagline b { font-weight: 800; }

  .hero-art {
    position: absolute; top: 290px; left: 150px; width: 620px; height: 400px;
    border-radius: 50% 50% 12px 12px / 30% 30% 12px 12px;
    background: radial-gradient(ellipse at 50% 60%, #d4e6fa 0%, #e9f2fd 55%, rgba(255,255,255,0) 80%);
  }
  .remote-badge {
    position: absolute; top: 340px; left: 178px; width: 150px; height: 110px;
    border-radius: 50%;
    background: var(--navy);
    color: var(--white);
    font-family: "Montserrat", Arial, sans-serif;
    font-style: italic; font-weight: 800; font-size: 22px; line-height: 1.1;
    display: flex; align-items: center; justify-content: center; text-align: center;
  }

  .audience {
    position: absolute; top: 700px; left: 0; width: 100%;
    text-align: center;
    font-family: "Montserrat", Arial, sans-serif;
    font-weight: 600; font-size: 22px; line-height: 1.4;
    color: var(--navy);
  }
  .session {
    position: absolute; top: 762px; left: 0; width: 100%;
    text-align: center;
    font-family: "Montserrat", Arial, sans-serif;
    font-weight: 900; font-size: 64px; line-height: 1;
    color: var(--navy);
  }
  .session sup { font-size: 30px; vertical-align: 28px; }
  .start-date {
    position: absolute; top: 830px; left: 0; width: 100%;
    text-align: center;
    font-family: "Montserrat", Arial, sans-serif;
    font-weight: 800; font-size: 40px; line-height: 1.2;
    color: var(--navy);
  }

  .topics {
    position: absolute; top: 900px; left: 58px; width: 770px;
    display: grid; grid-template-columns: 270px 270px 230px;
    row-gap: 12px;
    list-style: none;
  }
  .topics li {
    display: flex; align-items: center; gap: 12px;
    font-size: 19px; font-weight: 500; color: var(--ink);
    white-space: nowrap;
  }
  .topics li::before {
    content: ""; width: 16px; height: 16px; flex: none;
    background: var(--blue); border-radius: 2px;
  }

  .footer {
    position: absolute; left: 0; bottom: 0; width: 100%; height: 72px;
    background: var(--sky);
    display: flex; align-items: center; justify-content: center; gap: 14px;
    font-family: "Montserrat", Arial, sans-serif;
    font-weight: 700; font-size: 22px; color: var(--navy);
  }
  .footer .divider { color: var(--blue); }
</style>
</head>
<body>
<main class="flyer">
  <svg class="corner-wave" viewBox="0 0 360 230" aria-hidden="true">
    <path d="M140 0 C170 70 250 110 360 120 L360 0 Z" fill="#2b86ea"/>
    <path d="M60 0 C110 120 240 190 360 190 L360 150 C250 140 170 90 130 0 Z" fill="#dcecfb"/>
  </svg>

  <h1 class="course-title">REAL ESTATE COURSE</h1>
  <p class="headline">How To Make <span class="accent">Money In</span> In Real Estate?</p>
  <p class="tagline">An Investment <b>In Knowledge</b> Opens Up Untold Opportunities</p>

  <div class="hero-art" role="img" aria-label="Illustration of a young man in a blue suit standing beside a white two-storey house with trees"></div>
  <div class="remote-badge">Remote<br>Sessions</div>

  <p class="audience">For Those Who Have Started Or Would Like To Go<br>Into Real Estate</p>
  <p class="session">12<sup>TH</sup> SESSION</p>
  <p class="start-date">IN STARTING JUNE 16</p>

  <ul class="topics">
    <li>Single-family</li>
    <li>Real Estate law</li>
    <li>Foreclosures</li>
    <li>Multifamily</li>
    <li>Investment properties</li>
    <li>Short sales</li>
    <li>Management</li>
    <li>Foreclosures</li>
    <li>Development</li>
    <li>Real Estate Concepts</li>
    <li>Rehab</li>
    <li>Finical modeling</li>
    <li>HUD properties</li>
    <li>Due Diligence e</li>
  </ul>

  <footer class="footer">
    <span>0800 555 010</span><span class="divider">|</span>
    <span>propertylearning.info</span><span class="divider">|</span>
    <span>propertylearning.com</span>
  </footer>
</main>
</body>
</html>
```